Veltrane Group Business Card Design

The CEO is looking for a new trendy look for his business card.
You can stay with current branding or come up with something new/creative. It can be 3D, including Medical Office buildings. You can use our logo in a variety of colors. Please include name, title, company name, company website, email address, cell number

Target Market(s)

Real Estate Development and Construction

Industry/Entity Type

Health care real estate

Contact Information for Business Card

Rohesh Kamdar, CEO M-604.781.2249 E-roheshkamdar@veltrane.com Address:4180 Lindqvist Ave, Tampa, FL 33482 www.veltrane.com

Font styles to use
Other font styles liked:
• Be creative

Requirements
Must have
• Creative, trendy look
Nice to have
• Please go to our website to get a feel- www. veltrane.com
Should not have
• small fonts

```html
<!DOCTYPE html>
<html lang="en">
<head>
<meta charset="UTF-8">
<title>Veltrane Group Business Card</title>
<link href="https://fonts.googleapis.com/css2?family=Montserrat:wght@400;700;800&display=swap" rel="stylesheet">
<style>
  :root {
    --bg: #2b2b2b;
    --card: #ffffff;
    --ink: #111111;
    --muted: #333333;
    --rule: #1a1a1a;
  }
  * { margin: 0; padding: 0; box-sizing: border-box; }
  html, body {
    width: 1200px; height: 875px; overflow: hidden;
    background: var(--bg);
    font-family: "Montserrat", sans-serif;
    color: var(--ink);
  }
  .stage { position: relative; width: 1200px; height: 875px; }
  .card {
    position: absolute;
    width: 600px; height: 350px;
    background: var(--card);
    border-radius: 22px;
  }
  .card-front { left: 110px; top: 55px; display: flex; align-items: center; justify-content: center; }
  .card-back { left: 490px; top: 470px; }

  .brand-name {
    font-weight: 800;
    letter-spacing: -1px;
    color: var(--ink);
    white-space: nowrap;
  }
  .card-front .brand-name { font-size: 66px; }
  .card-back .brand-name {
    position: absolute; right: 40px; top: 48px;
    font-size: 36px;
  }
  .header-rule {
    position: absolute; left: 220px; right: 40px; top: 108px;
    border-top: 1px solid var(--rule);
  }
  .address {
    position: absolute; right: 40px; top: 124px;
    text-align: right; font-size: 13px; line-height: 1.35; color: var(--muted);
  }
  .person { position: absolute; left: 40px; bottom: 40px; }
  .person-name { font-size: 24px; font-weight: 700; }
  .person-title { font-size: 14px; margin-top: 2px; color: var(--muted); }
  .person-rule { width: 200px; border-top: 1px solid var(--rule); margin: 8px 0 10px; }
  .contact-list { list-style: none; font-size: 14px; color: var(--muted); }
  .contact-list li { display: flex; align-items: center; gap: 10px; line-height: 1.7; }
  .contact-list svg { width: 13px; height: 13px; fill: var(--ink); flex: none; }
</style>
</head>
<body>
<main class="stage">
  <section class="card card-front">
    <span class="brand-name">Veltrane Group</span>
  </section>

  <section class="card card-back">
    <span class="brand-name">Veltrane Group</span>
    <div class="header-rule"></div>
    <p class="address">4180 Lindqvist Ave,<br>Tampa, FL 33482</p>

    <div class="person">
      <p class="person-name">Rohesh Kamdar</p>
      <p class="person-title">CEO</p>
      <div class="person-rule"></div>
      <ul class="contact-list">
        <li>
          <svg viewBox="0 0 24 24" aria-hidden="true"><path d="M6.6 10.8a15.5 15.5 0 0 0 6.6 6.6l2.2-2.2c.3-.3.7-.4 1-.2 1.1.4 2.3.6 3.6.6.6 0 1 .4 1 1V20c0 .6-.4 1-1 1A17 17 0 0 1 3 4c0-.6.4-1 1-1h3.5c.6 0 1 .4 1 1 0 1.3.2 2.5.6 3.6.1.3 0 .7-.2 1z"/></svg>
          604.781.2249
        </li>
        <li>
          <svg viewBox="0 0 24 24" aria-hidden="true"><path d="M2 5h20v14H2z M2 5l10 8 10-8" fill="none" stroke="#111" stroke-width="2"/><path d="M2 5h20L12 13z"/></svg>
          roheshkamdar@veltrane.com
        </li>
        <li>
          <svg viewBox="0 0 24 24" aria-hidden="true"><circle cx="12" cy="12" r="10" fill="none" stroke="#111" stroke-width="2"/><path d="M2 12h20M12 2c3 3 3 17 0 20M12 2c-3 3-3 17 0 20" fill="none" stroke="#111" stroke-width="1.6"/></svg>
          www.veltrane.com
        </li>
      </ul>
    </div>
  </section>
</main>
</body>
</html>
```